Carpentry framing business card and logo design

We need a logo that works well with baseball caps, tee shirts and sweat shirts. We are a carpentry framing company specializing in apartment complexes and large residential communities. We work in what is known as the tri state area southeastern Pennsylvania , New Jersey and northern Delaware . We would like to see die signs using the old English letter M and royal blue colors. Also we stress OSHA compliance and safety.

Industry/Entity Type

Residential

Contact Information for Business Card

Valdrick Construction Co Inc
4870 Quillford Lane
Ambler PA 19087
Dale Valdrick
dale1valdrick@norvexmail.com
267-815-0926

```html
<!DOCTYPE html>
<html lang="en">
<head>
<meta charset="utf-8">
<title>Valdrick Construction Co Inc – Business Card</title>
<link href="https://fonts.googleapis.com/css2?family=Arimo:wght@400;700&display=swap" rel="stylesheet">
<style>
  :root {
    --bg: #e9e7e3;
    --card-white: #fbfbfb;
    --brand-green: #52b848;
    --brand-green-light: #7fd06f;
    --ink: #1e1e1e;
    --ink-soft: #3a3a3a;
  }
  * { margin: 0; padding: 0; box-sizing: border-box; }
  html, body { width: 1200px; height: 818px; overflow: hidden; background: var(--bg); }
  .canvas {
    position: relative; width: 1200px; height: 818px;
    display: flex; align-items: center; justify-content: center; gap: 60px;
    font-family: "Arimo", Arial, sans-serif;
  }
  .card {
    position: relative; width: 520px; height: 298px; overflow: hidden;
    background: var(--card-white);
    box-shadow: 0 10px 28px rgba(0,0,0,.18);
  }
  .card-art { position: absolute; inset: 0; width: 100%; height: 100%; }
  .card-front .content { position: absolute; left: 34px; top: 34px; width: 330px; }
  .company-mark { display: flex; align-items: center; gap: 10px; }
  .company-mark .mark-square { width: 18px; height: 18px; background: var(--brand-green); }
  .company-name {
    font-size: 21px; font-weight: 400; color: var(--brand-green);
    letter-spacing: .5px; line-height: 1.1;
  }
  .tagline { margin-top: 22px; font-size: 16px; color: var(--ink); }
  .person-name { margin-top: 14px; font-size: 20px; color: var(--brand-green); }
  .contact-list { list-style: none; margin-top: 14px; }
  .contact-list li {
    display: flex; align-items: center; gap: 10px;
    font-size: 13.5px; color: var(--ink-soft); line-height: 22px;
  }
  .contact-list svg { width: 13px; height: 13px; flex: none; }
</style>
</head>
<body>
<main class="canvas">
  <!-- Front of card -->
  <section class="card card-front">
    <svg class="card-art" viewBox="0 0 520 298" aria-hidden="true">
      <path d="M350 0 C470 40 500 170 455 298 L520 298 L520 0 Z" fill="var(--brand-green)"/>
      <path d="M330 0 C455 40 488 170 440 298" fill="none" stroke="var(--ink)" stroke-width="5"/>
    </svg>
    <div class="content">
      <div class="company-mark">
        <span class="mark-square"></span>
        <span class="company-name">Valdrick Construction Co Inc</span>
      </div>
      <p class="tagline">OSHA compliance and SAFETY 1st</p>
      <p class="person-name">Dale Valdrick</p>
      <ul class="contact-list">
        <li>
          <svg viewBox="0 0 12 12"><circle cx="6" cy="3.5" r="2.5" fill="var(--brand-green)"/><path d="M1 12 C1 7 11 7 11 12 Z" fill="var(--brand-green)"/></svg>
          267-815-0926
        </li>
        <li>
          <svg viewBox="0 0 12 12"><rect x="0.5" y="2" width="11" height="8" fill="var(--brand-green)"/><path d="M0.5 2 L6 6.5 L11.5 2" fill="none" stroke="#fff" stroke-width="1"/></svg>
          dale1valdrick@norvexmail.com
        </li>
        <li>
          <svg viewBox="0 0 12 12"><path d="M6 12 C2 7 1.5 5.5 1.5 4.5 A4.5 4.5 0 0 1 10.5 4.5 C10.5 5.5 10 7 6 12 Z" fill="var(--brand-green)"/><circle cx="6" cy="4.5" r="1.6" fill="#fff"/></svg>
          4870 Quillford Lane Ambler PA 19087
        </li>
      </ul>
    </div>
  </section>

  <!-- Back of card -->
  <section class="card card-back">
    <svg class="card-art" viewBox="0 0 520 298" aria-hidden="true">
      <defs>
        <linearGradient id="backGreen" x1="0" y1="0" x2="1" y2="1">
          <stop offset="0" stop-color="var(--brand-green-light)"/>
          <stop offset="1" stop-color="var(--brand-green)"/>
        </linearGradient>
      </defs>
      <rect width="520" height="298" fill="url(#backGreen)"/>
      <ellipse cx="215" cy="149" rx="190" ry="132" fill="var(--card-white)"/>
      <path d="M60 60 C140 8 330 0 395 90 C440 150 410 240 330 275" fill="none" stroke="var(--ink)" stroke-width="5"/>
    </svg>
  </section>
</main>
</body>
</html>
```